Barrister at Law needs Business Card Design

Need a business card design for Barrister at Law. Double sided. Simple Neil Thorsby and Barrister at Law on one side with contact details on the other side. I would like a professional design using Black or Platinum. Details on reverse side would include qualifications - Bcom-Llb and Acc Spec Commercial Litigation. I have attached the logo. Contact details would include address/ Po Box/ Phone/Fax/Mobile/email. I would like to use raised print or spot gloss.

```html
<!DOCTYPE html>
<html lang="en">
<head>
<meta charset="utf-8">
<title>Neil Thorsby – Barrister-at-Law Business Card</title>
<link href="https://fonts.googleapis.com/css2?family=Cinzel:wght@400;600&family=Open+Sans:wght@400;600&display=swap" rel="stylesheet">
<style>
  :root {
    --backdrop: #3a3532;
    --card-black: #151516;
    --card-edge: #232325;
    --brand-blue: #2f78c4;
    --brand-blue-deep: #1d5fa8;
    --silver: #b9bcc0;
    --stripe-grey: #9a9da1;
    --text-white: #eef0f2;
    --rule-grey: #6e7175;
  }
  * { margin: 0; padding: 0; box-sizing: border-box; }
  html, body {
    width: 1200px; height: 814px; overflow: hidden;
    background: var(--backdrop);
  }
  .stage {
    position: relative; width: 1200px; height: 814px;
    display: flex; align-items: center; justify-content: center; gap: 50px;
  }
  .card {
    position: relative; width: 520px; height: 297px;
    background: var(--card-black);
    border: 1px solid var(--card-edge);
    box-shadow: 0 14px 30px rgba(0,0,0,0.45);
    overflow: hidden;
  }
  /* Front */
  .card-front {
    display: flex; flex-direction: column; align-items: center; justify-content: center;
  }
  .holder-name {
    font-family: "Cinzel", serif; font-weight: 600;
    font-size: 30px; letter-spacing: 1px; color: var(--brand-blue);
  }
  .holder-title {
    margin-top: 4px;
    font-family: "Cinzel", serif; font-weight: 400;
    font-size: 20px; letter-spacing: 1px; color: var(--silver);
  }
  /* Back */
  .contact-list {
    position: absolute; left: 24px; top: 112px;
    list-style: none;
    font-family: "Open Sans", sans-serif; font-size: 13px; color: var(--text-white);
  }
  .contact-list li { display: flex; align-items: center; gap: 9px; height: 21px; }
  .contact-list svg { width: 13px; height: 13px; fill: var(--brand-blue); flex: none; }
  .divider-rule {
    position: absolute; left: 160px; right: 30px; top: 196px;
    height: 1px; background: var(--rule-grey);
  }
  .accreditation-badge {
    position: absolute; right: 30px; top: 40px; width: 110px; height: 110px;
  }
  .address {
    position: absolute; right: 30px; top: 206px;
    font-family: "Open Sans", sans-serif; font-size: 13px; line-height: 19px;
    color: var(--text-white); text-align: right;
  }
  .accent-bands { position: absolute; left: 0; bottom: 0; width: 520px; height: 60px; }
  .website {
    position: absolute; right: 30px; bottom: 6px;
    font-family: "Open Sans", sans-serif; font-size: 14px; letter-spacing: 3px;
    color: var(--text-white);
  }
</style>
</head>
<body>
<main class="stage">
  <section class="card card-front" aria-label="Card front">
    <h1 class="holder-name">Neil Thorsby</h1>
    <p class="holder-title">Barrister-at-Law</p>
  </section>

  <section class="card card-back" aria-label="Card back">
    <ul class="contact-list">
      <li>
        <svg viewBox="0 0 16 16"><path d="M3.6 1.5l2.3 2.6-1.3 1.8c.9 2 2.5 3.6 4.5 4.5l1.8-1.3 2.6 2.3-1.4 2.3C6.7 13.7 2.3 9.3 1.3 3z"/></svg>
        <span>612 405 7719</span>
      </li>
      <li>
        <svg viewBox="0 0 16 16"><path d="M4.5 1h7a1 1 0 0 1 1 1v12a1 1 0 0 1-1 1h-7a1 1 0 0 1-1-1V2a1 1 0 0 1 1-1zm.6 2v9h5.8V3zM8 12.6a.8.8 0 1 0 0 1.6.8.8 0 0 0 0-1.6z"/></svg>
        <span>612 405 7720</span>
      </li>
      <li>
        <svg viewBox="0 0 16 16"><path d="M4 1h6l2 2v3H4zM2 7h12a1 1 0 0 1 1 1v5a1 1 0 0 1-1 1H2a1 1 0 0 1-1-1V8a1 1 0 0 1 1-1zm9 2v1.5h2V9z"/></svg>
        <span>612 405 7721</span>
      </li>
      <li>
        <svg viewBox="0 0 16 16"><path d="M1 3h14v1.2L8 9 1 4.2zm0 2.6l7 4.8 7-4.8V13H1z"/></svg>
        <span>neil@thorsbylaw.com</span>
      </li>
    </ul>

    <svg class="accreditation-badge" viewBox="0 0 110 110" role="img" aria-label="Accredited specialist badge">
      <circle cx="55" cy="55" r="52" fill="var(--text-white)"/>
      <circle cx="55" cy="55" r="47" fill="var(--card-black)"/>
      <circle cx="55" cy="55" r="24" fill="var(--brand-blue)"/>
    </svg>

    <div class="divider-rule"></div>

    <address class="address" style="font-style:normal">
      14 Harrowgate Lane<br>
      Westbury, Alder 41820
    </address>

    <svg class="accent-bands" viewBox="0 0 520 60" preserveAspectRatio="none" aria-hidden="true">
      <polygon points="0,12 238,12 254,24 0,24" fill="var(--stripe-grey)"/>
      <polygon points="0,27 256,27 270,30 520,30 520,60 0,60" fill="var(--brand-blue)"/>
      <polygon points="0,27 256,27 262,30 0,34" fill="var(--brand-blue-deep)"/>
    </svg>
    <p class="website">www.thorsbylaw.com</p>
  </section>
</main>
</body>
</html>
```